Small legal and financial translation company needs Squarespace website, brochure and logo

Hello,
We are Lumarin Services (www.lumarinservices-example.com), a boutique legal and financial translation company. We offer our services mainly to Spanish customers. Our primary line of business is the translation of financial statements, but we translate a wide variety legal and financial texts.
The project we are offering comprises three parts: a redo of the current website, an informational brochure for potential customer and a logo design. These three parts should provide a consistent image. We would develop content soon.
We are looking for a website that would look like a typical law firm website, nothing too fancy. Right now, it is in English, Spanish and French, although the new site need only be in English and Spanish. There must be good toggling between the English and Spanish versions. There would be no need for tie-ins to social media and it would not contain a blog. Basically, a static site. We aren't interesting in driving traffic to the site or SEO, as we will contact nearly all potential customers beforehand. The website must be built in Squarespace to enable a smooth transition. The content would be similar to the current page, we'll be working on the exact content, but a rough draft is attached.
The brochure will be some three pages and would introduce the company to potential customers, using similar images as the website and the logo to be designed.
The only specifications for the logo is, as the website and brochure, it convey a sense of security and trust.
Feel free to ask with any questions as this is the first time we have used this platform.
Thank you!
Updates

I've added a more or less final version for the text in the brochure and updated the brief. Added Wednesday, June 10, 2015

Target Market(s)

Spanish law firms, auditors, accountants, banks, investment firms

Industry/Entity Type

Finance

Logo Text

Lumarin Services

Number of Pages Required

5+ page

Font styles to use
Serif

Requirements
Must have
• The website must be built in Squarespace and have a good option to toggle between English and Spanish versions.
• Brochure must be in both English and Spanish, I'm attaching a rough draft of the information that it will probably have. This should give an idea about what to include and the spacing. I will update it to include the final information.
Nice to have
• Would be nice to have some quality finance- and legal-related images
Should not have
• Vibrant colours

```html
<!DOCTYPE html>
<html lang="en">
<head>
<meta charset="utf-8">
<title>Lumarin Services – Financial translation brochure spread</title>
<link rel="stylesheet" href="https://fonts.googleapis.com/css2?family=Playfair+Display:ital,wght@1,700&family=Sorts+Mill+Goudy&display=swap">
<style>
  :root {
    --backdrop: #e9e6e1;
    --page-dark: #262626;
    --page-dark-edge: #1b1b1b;
    --page-dark-glow: #3a3a3a;
    --accent-blue: #a9dbe9;
    --accent-band: #5c7078;
    --text-light: #f1f1f1;
    --rule: #e8e8e8;
    --photo-light: #d9d6d2;
    --photo-mid: #9b9894;
    --photo-dark: #3d3b39;
  }
  * { box-sizing: border-box; margin: 0; padding: 0; }
  html, body { width: 1200px; height: 537px; overflow: hidden; }
  body { background: var(--backdrop); position: relative; font-family: "Sorts Mill Goudy", Georgia, serif; }

  .spread {
    position: absolute; left: 55px; top: 75px; width: 1105px; height: 390px;
    box-shadow: 0 4px 14px rgba(0,0,0,.25);
  }

  /* left page */
  .page-left { position: absolute; left: 0; top: 0; width: 552px; height: 390px; }
  .hero-photo {
    position: absolute; inset: 0 0 8px 0;
    background:
      radial-gradient(ellipse at 70% 25%, rgba(255,255,255,.55), transparent 55%),
      linear-gradient(160deg, var(--photo-light) 0%, var(--photo-mid) 45%, var(--photo-dark) 100%);
  }
  .page-left .edge-band { position: absolute; left: 0; bottom: 0; width: 100%; height: 8px; background: var(--accent-blue); }

  /* right page */
  .page-right {
    position: absolute; left: 555px; top: 0; width: 550px; height: 390px;
    background:
      radial-gradient(ellipse at 25% 45%, var(--page-dark-glow), transparent 60%),
      linear-gradient(90deg, var(--page-dark-edge), var(--page-dark) 30%, var(--page-dark) 80%, var(--page-dark-edge));
    color: var(--text-light);
  }
  .page-right .edge-band { position: absolute; left: 0; bottom: 0; width: 100%; height: 8px; background: var(--accent-band); }

  .brand-name {
    position: absolute; left: 48px; top: 20px;
    font-family: "Sorts Mill Goudy", Georgia, serif; font-size: 20px; color: var(--accent-blue);
  }

  .section { position: absolute; right: 23px; }
  .section-en { top: 24px; width: 267px; }
  .section-es { top: 193px; width: 277px; }
  .section-title {
    font-family: "Playfair Display", Georgia, serif; font-style: italic; font-weight: 700;
    font-size: 20px; text-align: right; line-height: 26px; padding-right: 2px;
    border-bottom: 2px solid var(--rule); padding-bottom: 1px;
  }
  .section-intro {
    color: var(--accent-blue); font-size: 17px; line-height: 16px;
    margin-top: 10px; padding-left: 2px;
  }
  .section-es .section-intro { padding-left: 12px; }
  .service-lists { display: flex; margin-top: 7px; padding-left: 6px; }
  .section-es .service-lists { padding-left: 16px; }
  .service-list { list-style: none; font-size: 10.5px; line-height: 11px; }
  .service-list:first-child { width: 114px; }
  .service-list li { position: relative; padding-left: 9px; margin-bottom: 5px; }
  .service-list li::before {
    content: ""; position: absolute; left: 0; top: 4px; width: 3px; height: 3px;
    border-radius: 50%; background: var(--text-light);
  }

  .detail-photo {
    position: absolute; left: 48px; width: 115px;
    border: 1px solid #555;
    background: linear-gradient(135deg, var(--photo-light), var(--photo-mid) 55%, var(--photo-dark));
  }
  .detail-photo.handshake { top: 216px; height: 76px; }
  .detail-photo.paperwork { top: 300px; height: 69px; }
</style>
</head>
<body>
  <div class="spread">
    <section class="page-left">
      <div class="hero-photo" role="img" aria-label="Black and white photo of business people talking by an office window, with a laptop, pens and financial charts on a desk in the foreground"></div>
      <div class="edge-band"></div>
    </section>

    <section class="page-right">
      <div class="brand-name">Lumarin Services</div>

      <div class="section section-en">
        <h2 class="section-title">Financial translation</h2>
        <p class="section-intro">Financial translation includes but is not limited to:</p>
        <div class="service-lists">
          <ul class="service-list">
            <li>financial statements and notes</li>
            <li>annual reports</li>
            <li>auditor’s reports</li>
            <li>director’s reports</li>
            <li>limited reviews</li>
          </ul>
          <ul class="service-list">
            <li>business plans</li>
            <li>macroeconomic reports</li>
            <li>investment fund reports</li>
            <li>annual banking reports</li>
            <li>financing agreements</li>
          </ul>
        </div>
      </div>

      <div class="section section-es" lang="es">
        <h2 class="section-title">Traducción Financiera</h2>
        <p class="section-intro">Traducción financiera incluye pero no se limita a:</p>
        <div class="service-lists">
          <ul class="service-list">
            <li>estados financieros y notas</li>
            <li>informes anuales</li>
            <li>informes de auditoría</li>
            <li>informes del director</li>
            <li>revisiones limitadas</li>
          </ul>
          <ul class="service-list">
            <li>planes de negocios</li>
            <li>informes macroeconómicos</li>
            <li>informes de fondos de inversión</li>
            <li>informes bancarios anuales</li>
            <li>acuerdos de financiación</li>
          </ul>
        </div>
      </div>

      <div class="detail-photo handshake" role="img" aria-label="Black and white photo of a business handshake"></div>
      <div class="detail-photo paperwork" role="img" aria-label="Black and white photo of a hand reviewing documents beside a calculator"></div>

      <div class="edge-band"></div>
    </section>
  </div>
</body>
</html>
```